New Bicycle shop business card

Hi!
I'm looking for a business card for my new proffesional bike mechanics shop. This shop is only for fixing broken bikes and not selling bikes.
Peferbly a modern and sleek and modern design.
Colors: black, grey, red, white
Information:
Name: Rijwielwerkplaats Vanhoutte
Shop owner: Bart Vanhoutte & Marieke Segers
Website: www.rijwielwerkplaats-vanhoutte.be
Email: info@rijwielwerkplaats-vanhoutte.be
Phone number: +32471902368
Street adres: Kerkweg 46
9940 Bellebeke
Slogan/shop information: Herstellingen van alle merken.
Logo: see files.
Target Market(s)
People who seek a mechanic to fix or upgrade their bikes.
Contact Information for Business Card
Information:
Website: info@rijwielwerkplaats-vanhoutte.be
9940 Bellebeke
Logo: see files.

```html
<!DOCTYPE html>
<html lang="nl">
<head>
<meta charset="utf-8">
<title>Rijwielwerkplaats Vanhoutte – Business Card</title>
<link rel="stylesheet" href="https://fonts.googleapis.com/css2?family=Montserrat:wght@800&family=Roboto:wght@400&display=swap">
<style>
  :root {
    --backdrop: #3b3b3d;
    --card-black: #1e1e20;
    --brand-red: #e02b3c;
    --stripe-grey: #9a9c9e;
    --text-white: #ffffff;
    --text-soft: #e6e6e6;
  }
  * { box-sizing: border-box; margin: 0; padding: 0; }
  html, body {
    width: 799px; height: 1200px; overflow: hidden;
    background: var(--backdrop);
  }
  .sheet {
    position: relative; width: 799px; height: 1200px;
  }
  .card {
    position: absolute; left: 50px; width: 700px; height: 400px;
    background: var(--card-black);
    border-radius: 24px; overflow: hidden;
    box-shadow: 0 12px 30px rgba(0,0,0,0.45);
  }
  .card--front { top: 110px; }
  .card--back { top: 680px; }

  .brand {
    display: flex; flex-direction: column; align-items: center;
  }
  .brand__mark {
    width: 44px; height: 44px; background: var(--brand-red);
    margin-bottom: 14px;
  }
  .brand__name {
    font-family: 'Montserrat', sans-serif; font-weight: 800;
    color: var(--text-white); text-transform: uppercase;
    text-align: center; line-height: 1.1; letter-spacing: 1px;
  }
  .card--front .brand {
    position: absolute; top: 88px; left: 0; right: 0;
  }
  .card--front .brand__name { font-size: 36px; }
  .website {
    position: absolute; left: 0; right: 0; top: 300px;
    text-align: center;
    font-family: 'Roboto', sans-serif; font-size: 19px;
    color: var(--text-soft);
  }
  .website__accent { color: var(--brand-red); }

  .card--back .brand {
    position: absolute; top: 36px; left: 40px; width: 330px;
  }
  .card--back .brand__mark { width: 38px; height: 38px; margin-bottom: 12px; }
  .card--back .brand__name { font-size: 26px; }

  .person {
    position: absolute; top: 105px; right: 42px; text-align: right;
  }
  .person__name {
    font-family: 'Montserrat', sans-serif; font-weight: 800;
    font-size: 22px; letter-spacing: 1px; text-transform: uppercase;
    color: var(--brand-red);
  }
  .person__role {
    font-family: 'Roboto', sans-serif; font-size: 15px;
    color: var(--text-white); margin-top: 4px;
  }
  .wave { position: absolute; left: 0; top: 0; width: 700px; height: 400px; }

  .contact {
    position: absolute; right: 36px; top: 270px;
    list-style: none; text-align: right;
    font-family: 'Roboto', sans-serif; font-size: 16px;
    color: var(--text-white);
  }
  .contact__item {
    display: flex; justify-content: flex-end; align-items: center;
    gap: 10px; height: 25px;
  }
  .contact__icon { width: 15px; height: 15px; flex: none; }
</style>
</head>
<body>
<main class="sheet">

  <section class="card card--front" aria-label="Card front">
    <div class="brand">
      <div class="brand__mark"></div>
      <div class="brand__name">Rijwielwerkplaats<br>Vanhoutte</div>
    </div>
    <p class="website">www.rijwielwerkplaats-<span class="website__accent">vanhoutte</span>.be</p>
  </section>

  <section class="card card--back" aria-label="Card back">
    <svg class="wave" viewBox="0 0 700 400" aria-hidden="true">
      <path d="M0,192 C170,178 300,282 450,248 C560,224 640,200 700,188"
            fill="none" stroke="var(--stripe-grey)" stroke-width="9"/>
      <path d="M0,178 C170,166 290,250 420,236"
            fill="none" stroke="var(--stripe-grey)" stroke-width="2" opacity="0.7"/>
      <path d="M0,215 C170,202 300,300 450,268 C560,246 640,230 700,222 L700,400 L0,400 Z"
            fill="var(--brand-red)"/>
    </svg>

    <div class="brand">
      <div class="brand__mark"></div>
      <div class="brand__name">Rijwielwerkplaats<br>Vanhoutte</div>
    </div>

    <div class="person">
      <p class="person__name">Marieke Segers</p>
      <p class="person__role">Owner</p>
    </div>

    <ul class="contact">
      <li class="contact__item">+32471902368
        <svg class="contact__icon" viewBox="0 0 16 16" aria-hidden="true"><path fill="#fff" d="M3.5 1.5l2.5 0 1 3.5-1.7 1.2a9 9 0 0 0 4.5 4.5L11 9l3.5 1v2.5c0 1-1 2-2 2C6.5 14.5 1.5 9.5 1.5 3.5c0-1 1-2 2-2z"/></svg>
      </li>
      <li class="contact__item">info@rijwielwerkplaats-vanhoutte.be
        <svg class="contact__icon" viewBox="0 0 16 16" aria-hidden="true"><rect x="1" y="3" width="14" height="10" fill="#fff"/><path d="M1 3l7 6 7-6" fill="none" stroke="var(--brand-red)" stroke-width="1.4"/></svg>
      </li>
      <li class="contact__item">www.rijwielwerkplaats-vanhoutte.be
        <svg class="contact__icon" viewBox="0 0 16 16" aria-hidden="true"><g fill="none" stroke="#fff" stroke-width="1.4"><circle cx="8" cy="8" r="6.5"/><ellipse cx="8" cy="8" rx="3" ry="6.5"/><path d="M1.5 8h13M2.5 4.8h11M2.5 11.2h11"/></g></svg>
      </li>
      <li class="contact__item">Kerkweg 46 9940 Bellebeke
        <svg class="contact__icon" viewBox="0 0 16 16" aria-hidden="true"><path fill="#fff" d="M8 1a5 5 0 0 0-5 5c0 3.8 5 9 5 9s5-5.2 5-9a5 5 0 0 0-5-5zm0 7a2 2 0 1 1 0-4 2 2 0 0 1 0 4z"/></svg>
      </li>
    </ul>
  </section>

</main>
</body>
</html>
```